Kestrada LLC, needs a web page no more than 5 pages (for now)

Kestrada is a general contractor. Our services include general contracting, design-build construction, disaster recovery and environmental remediation. Our main clients are PMX, TQ, State and Local Gov't Agencies, Hospitals and Schools. Kestrada is also a SDVOSB.

```html
<!DOCTYPE html>
<html lang="en">
<head>
<meta charset="utf-8">
<title>Kestrada LLC — General Contracting</title>
<link href="https://fonts.googleapis.com/css2?family=Archivo+Black&family=Roboto:ital,wght@0,400;0,500;0,700;1,400&display=swap" rel="stylesheet">
<style>
:root{
  --gold:#c9914a;
  --gold-dark:#a8742f;
  --gold-light:#e2b86c;
  --ink:#1b1b1b;
  --text:#666;
  --grey:#eeeeee;
  --footer:#0b0b0b;
  --white:#fff;
}
*{margin:0;padding:0;box-sizing:border-box}
html,body{width:1200px;height:3214px;overflow:hidden}
body{position:relative;background:var(--white);font-family:"Roboto",sans-serif;color:var(--ink)}
.abs{position:absolute}
.heading{font-family:"Archivo Black",sans-serif;font-weight:400;letter-spacing:-.5px;text-transform:uppercase}
.underline{position:absolute;height:3px;width:74px;background:var(--gold)}
.btn{position:absolute;display:flex;align-items:center;justify-content:center;background:linear-gradient(90deg,var(--gold-dark),var(--gold-light));color:var(--white);font-weight:700;font-size:15px;text-transform:uppercase}

/* header */
.site-header{position:absolute;left:0;top:0;width:1200px;height:128px}
.brand{position:absolute;left:112px;top:46px;display:flex;align-items:center;gap:10px;font-weight:700;font-size:28px;color:var(--ink)}
.brand .dot{width:22px;height:22px;border-radius:50%;background:var(--gold)}
.nav a{position:absolute;top:56px;font-size:13.5px;font-weight:700;color:var(--ink);text-decoration:none}
.nav a.active{color:var(--gold);border-bottom:1px solid var(--gold);padding-bottom:2px;width:66px}
.call-panel{position:absolute;right:0;top:0;width:339px;height:128px}
.call-label{position:absolute;left:1064px;top:38px;font-size:12.5px;color:var(--ink)}
.call-number{position:absolute;left:948px;top:74px;font-size:26px;font-weight:500;color:var(--ink)}

/* hero */
.hero-title{position:absolute;left:0;width:1200px;top:350px;text-align:center;color:var(--white);font-size:46px;line-height:53px}
.hero-sub{position:absolute;left:0;width:1200px;top:460px;text-align:center;color:var(--white);font-size:18.5px;line-height:27px;font-weight:500}
.dots span{position:absolute;left:1137px;width:12px;height:12px;border:2px solid var(--white);border-radius:50%}
.dots span.on{background:var(--white)}

/* about */
.about-frame{position:absolute;left:111px;top:821px;width:283px;height:224px;border:8px solid #d9d9d9;border-right:none;border-bottom:none}
.about-frame::after{content:"";position:absolute;left:-8px;top:0;width:8px;height:224px;background:#d9d9d9}
.photo{position:absolute}
.about-title{position:absolute;left:601px;top:893px;font-size:42px}
.about-lead{position:absolute;left:601px;top:968px;width:487px;font-size:14.5px;font-style:italic;line-height:25px;color:var(--ink);text-align:justify}
.about-body{position:absolute;left:601px;top:1051px;width:487px;font-size:15px;line-height:25px;color:var(--text);text-align:justify}

.section-title{position:absolute;left:0;width:1200px;text-align:center;font-size:42px}

/* services */
.service-label{position:absolute;color:var(--white);font-weight:700;font-size:18.5px;text-align:center;line-height:26px;text-transform:uppercase}

/* clients */
.client-card{position:absolute;top:2111px;width:171px;height:95px;background:var(--white);box-shadow:0 3px 10px rgba(0,0,0,.12);display:flex;align-items:center;justify-content:center;gap:7px;font-size:12px;font-weight:700;color:#3a3a3a;text-transform:uppercase}
.client-card .mark{width:14px;height:14px;border-radius:50%;background:#3a3a3a}

/* testimonials */
.testimonials{position:absolute;left:0;top:2313px;width:1200px;height:496px;background:linear-gradient(135deg,#c48e45 0%,#d9a95e 45%,#c08b45 100%)}
.t-card{position:absolute;top:2472px;width:312px;height:259px;background:var(--white);padding:28px 21px 0}
.stars{color:#8e5f25;font-size:14px;letter-spacing:2px}
.t-text{margin-top:8px;font-size:14.5px;line-height:22px;color:var(--text);text-align:justify}
.t-rule{margin-top:16px;height:1px;background:#cfcfcf}
.t-person{display:flex;align-items:center;gap:20px;margin-top:15px}
.avatar{width:56px;height:56px;border-radius:50%;background:linear-gradient(135deg,#d8cfc4,#9c8f80)}
.t-name{font-size:16px;font-weight:500;color:var(--ink);text-transform:uppercase}
.t-time{font-size:12px;color:var(--text);margin-top:5px}

/* footer */
.site-footer{position:absolute;left:0;top:2809px;width:1200px;height:405px;background:var(--footer);color:var(--white)}
.f-head{position:absolute;top:70px;font-size:16px;font-weight:700;text-transform:uppercase}
.f-mission{position:absolute;left:110px;top:101px;width:430px;font-size:13.5px;line-height:23px}
.f-links{position:absolute;left:606px;top:98px;list-style:none}
.f-links li{font-size:15px;height:31px;display:flex;align-items:center;gap:14px}
.f-links li::before{content:"»";color:var(--gold);font-weight:700}
.f-contact{position:absolute;left:831px;display:flex;align-items:center;gap:16px;font-size:15px;line-height:20px}
.f-icon{width:36px;height:36px;border-radius:50%;background:var(--white);display:flex;align-items:center;justify-content:center;flex-shrink:0}
.f-rule{position:absolute;left:110px;width:978px;height:1px;background:#2b2b2b}
.f-brand{position:absolute;left:112px;top:294px;display:flex;align-items:center;gap:8px;font-size:20px;font-weight:700}
.f-brand .dot{width:16px;height:16px;border-radius:50%;background:var(--gold)}
.f-legal{position:absolute;right:112px;top:295px;font-size:13.5px}
.f-copy{position:absolute;left:0;width:1200px;top:362px;text-align:center;font-size:12.5px}
.social{position:absolute;top:352px;width:38px;height:38px;border-radius:50%;background:var(--white);display:flex;align-items:center;justify-content:center;font-size:9px;font-weight:700;color:var(--ink)}
.social.gold{background:var(--gold);color:var(--white)}
</style>
</head>
<body>

<!-- Header -->
<header class="site-header">
  <div class="brand"><span class="dot"></span>Kestrada</div>
  <nav class="nav">
    <a class="active" style="left:357px">HOME</a>
    <a style="left:432px">ABOUT US</a>
    <a style="left:533px">OUR SERVICES</a>
    <a style="left:665px">PROJECTS</a>
    <a style="left:770px">CONTACT US</a>
  </nav>
  <svg class="call-panel" style="left:861px" width="339" height="128" viewBox="0 0 339 128">
    <polygon points="100,0 339,0 339,128 0,128" fill="#ececec"/>
    <circle cx="169" cy="44" r="20" fill="#c9914a"/>
    <path d="M162 36c2-1 3 0 4 3l1 2c0 1-1 2-2 3 1 3 3 5 6 6 1-1 2-2 3-2l2 1c3 1 4 2 3 4-1 3-4 4-7 3-5-2-9-6-11-11-1-3 0-7 1-9z" fill="#fff"/>
  </svg>
  <div class="call-label">CALL US TODAY!</div>
  <div class="call-number">+1 (555) 014 2290</div>
</header>

<!-- Hero -->
<section class="hero">
  <svg class="abs" style="left:0;top:128px" width="1200" height="643" viewBox="0 0 1200 643">
    <defs>
      <linearGradient id="heroPhoto" x1="0" y1="0" x2="1" y2="1">
        <stop offset="0" stop-color="#3e4a57"/>
        <stop offset=".5" stop-color="#7a7670"/>
        <stop offset="1" stop-color="#a99a85"/>
      </linearGradient>
      <linearGradient id="goldBand" x1="0" y1="0" x2="1" y2="0">
        <stop offset="0" stop-color="#a8742f"/>
        <stop offset=".5" stop-color="#e2b86c"/>
        <stop offset="1" stop-color="#b8843c"/>
      </linearGradient>
    </defs>
    <polygon role="img" aria-label="Photo of an engineer reviewing construction blueprints on a tablet beside building models" points="0,0 1200,0 1200,456 600,572 0,456" fill="url(#heroPhoto)"/>
    <polygon points="0,456 600,572 1200,456 1200,478 600,643 0,478" fill="url(#goldBand)"/>
    <polyline points="20,470 600,620 1180,470" fill="none" stroke="#fff" stroke-width="2.5"/>
  </svg>
  <h1 class="hero-title heading">Strength in Service<br>Excellence in Construction</h1>
  <p class="hero-sub">Kestrada is committed to delivering reliable, innovative, and sustainable<br>construction solutions with integrity and precision.</p>
  <div class="btn" style="left:530px;top:539px;width:141px;height:46px">Get Started</div>
  <div class="dots">
    <span style="top:331px"></span>
    <span class="on" style="top:354px"></span>
    <span style="top:378px"></span>
    <span style="top:402px"></span>
  </div>
</section>

<!-- About -->
<section class="about">
  <div class="about-frame"></div>
  <div class="photo" role="img" aria-label="Photo of two workers in hard hats overlooking a building site" style="left:140px;top:849px;width:354px;height:425px;background:linear-gradient(160deg,#d8a35c,#8b6a4a 55%,#5a4a3e)"></div>
  <div class="photo" style="left:344px;top:1120px;width:210px;height:209px;background:var(--white)"></div>
  <div class="photo" role="img" aria-label="Photo of a contractor shaking hands with clients on site" style="left:356px;top:1132px;width:192px;height:191px;background:linear-gradient(135deg,#4f6a86,#b7b9b8 60%,#d9d4c9)"></div>
  <h2 class="about-title heading">About Us</h2>
  <div class="underline" style="left:601px;top:942px;width:56px;height:2px"></div>
  <p class="about-lead">Kestrada is a Service-Disabled Veteran-Owned Small Business (SDVOSB) delivering construction excellence to government agencies, hospitals, and institutions nationwide.</p>
  <p class="about-body">Lorem ipsum dolor sit amet, consectetur adipiscing elit, sed do eiusmo tempor incididunt ut labore et dolore magna aliqua. Ut enim ad minim veniam, quis nostrud exercitation ullamco laboris nisi ut aliquip ex ea commodo consequat. Duis aute irure dolor in reprehenderit in voluptate velit esse cillum dolore eu fugiat nulla pariaturea.</p>
  <div class="btn" style="left:601px;top:1200px;width:142px;height:47px">Learn More</div>
</section>

<!-- Services -->
<section class="services">
  <h2 class="section-title heading" style="top:1410px">Our Services</h2>
  <div class="underline" style="left:563px;top:1458px"></div>
  <svg class="abs" style="left:0;top:1502px" width="1200" height="410" viewBox="0 0 1200 410">
    <defs>
      <linearGradient id="s1" x1="0" y1="0" x2="0" y2="1"><stop offset="0" stop-color="#8d8f94"/><stop offset="1" stop-color="#b08a3c"/></linearGradient>
      <linearGradient id="s2" x1="0" y1="0" x2="0" y2="1"><stop offset="0" stop-color="#9e968a"/><stop offset="1" stop-color="#6f6a62"/></linearGradient>
      <linearGradient id="s3" x1="0" y1="0" x2="0" y2="1"><stop offset="0" stop-color="#8b8a84"/><stop offset="1" stop-color="#5f5a50"/></linearGradient>
      <linearGradient id="s4" x1="0" y1="0" x2="0" y2="1"><stop offset="0" stop-color="#c9c6bf"/><stop offset="1" stop-color="#7d7a74"/></linearGradient>
    </defs>
    <polygon role="img" aria-label="Photo of a handshake over a yellow hard hat and plans" points="0,0 318,0 262,410 0,410" fill="url(#s1)"/>
    <polygon role="img" aria-label="Photo of an architectural building model beside a hard hat" points="318,0 620,0 564,410 262,410" fill="url(#s2)"/>
    <polygon role="img" aria-label="Photo of an inspector with a clipboard at a storm-damaged house" points="620,0 923,0 866,410 564,410" fill="url(#s3)"/>
    <polygon role="img" aria-label="Photo of a worker in protective suit treating mould on a wall" points="923,0 1200,0 1200,410 866,410" fill="url(#s4)"/>
    <line x1="318" y1="0" x2="262" y2="410" stroke="#fff" stroke-width="9"/>
    <line x1="620" y1="0" x2="564" y2="410" stroke="#fff" stroke-width="9"/>
    <line x1="923" y1="0" x2="866" y2="410" stroke="#fff" stroke-width="9"/>
  </svg>
  <div class="service-label" style="left:0;width:252px;top:1843px">General Contracting</div>
  <div class="service-label" style="left:317px;width:200px;top:1843px">Design-Build</div>
  <div class="service-label" style="left:600px;width:236px;top:1843px">Disaster Recovery</div>
  <div class="service-label" style="left:915px;width:240px;top:1831px">Environmental<br>Remediation</div>
</section>

<!-- Clients -->
<section class="clients">
  <h2 class="section-title heading" style="top:2019px">Our Clients</h2>
  <div class="underline" style="left:563px;top:2067px"></div>
  <svg class="abs" style="left:48px;top:2142px" width="20" height="32" viewBox="0 0 20 32"><polyline points="16,2 4,16 16,30" fill="none" stroke="#aaa" stroke-width="3"/></svg>
  <svg class="abs" style="left:1131px;top:2142px" width="20" height="32" viewBox="0 0 20 32"><polyline points="4,2 16,16 4,30" fill="none" stroke="#c9914a" stroke-width="3"/></svg>
  <div class="client-card" style="left:112px"><span class="mark"></span>Carewell Clinic</div>
  <div class="client-card" style="left:313px"><span class="mark"></span>PMX</div>
  <div class="client-card" style="left:514px">TQ</div>
  <div class="client-card" style="left:716px"><span class="mark"></span>Stateline</div>
  <div class="client-card" style="left:917px"><span class="mark"></span>Learnbridge</div>
</section>

<!-- Testimonials -->
<section class="testimonials" role="img" aria-label="Warm gold background with a faint photo of people at work"></section>
<h2 class="section-title heading" style="top:2380px;color:var(--white)">Testimonials</h2>
<div class="underline" style="left:563px;top:2428px;background:var(--white)"></div>
<svg class="abs" style="left:48px;top:2585px" width="20" height="32" viewBox="0 0 20 32"><polyline points="16,2 4,16 16,30" fill="none" stroke="#e9d3ad" stroke-width="3"/></svg>
<svg class="abs" style="left:1131px;top:2585px" width="20" height="32" viewBox="0 0 20 32"><polyline points="4,2 16,16 4,30" fill="none" stroke="#fff" stroke-width="3"/></svg>

<article class="t-card" style="left:111px">
  <div class="stars">★★★★★</div>
  <p class="t-text">Lorem ipsum dolor sit amet, consect adipiscing elit, sed do eiusmod temp incididunt ut labore et dolore magna aliqua ut enim ad minimea.</p>
  <div class="t-rule"></div>
  <div class="t-person"><div class="avatar" role="img" aria-label="Client portrait"></div><div><div class="t-name">Mara Ellison,</div><div class="t-time">1 year ago</div></div></div>
</article>
<article class="t-card" style="left:444px">
  <div class="stars">★★★★★</div>
  <p class="t-text">Lorem ipsum dolor sit amet, consect adipiscing elit, sed do eiusmod temp incididunt ut labore et dolore magna aliqua ut enim ad minimea.</p>
  <div class="t-rule"></div>
  <div class="t-person"><div class="avatar" role="img" aria-label="Client portrait"></div><div><div class="t-name">Dane Corwin,</div><div class="t-time">1 year ago</div></div></div>
</article>
<article class="t-card" style="left:776px">
  <div class="stars">★★★★★</div>
  <p class="t-text">Lorem ipsum dolor sit amet, consect adipiscing elit, sed do eiusmod temp incididunt ut labore et dolore magna aliqua ut enim ad minimea.</p>
  <div class="t-rule"></div>
  <div class="t-person"><div class="avatar" role="img" aria-label="Client portrait"></div><div><div class="t-name">Mara Ellison,</div><div class="t-time">1 year ago</div></div></div>
</article>

<!-- Footer -->
<footer class="site-footer">
  <div class="f-head" style="left:110px">Our Mission</div>
  <p class="f-mission">Our mission is to serve those who serve. Kestrada combines veteran leadership, technical expertise, and a commitment to quality to provide construction and recovery solutions that support the missions of government, healthcare, and education.</p>

  <div class="f-head" style="left:606px">Quick Links</div>
  <ul class="f-links">
    <li>Home</li><li>About Us</li><li>Our Services</li><li>Projects</li><li>Contact Us</li>
  </ul>

  <div class="f-head" style="left:831px">Contact Us</div>
  <div class="f-contact" style="top:100px">
    <span class="f-icon"><svg width="14" height="18" viewBox="0 0 14 18"><path d="M7 0C3 0 0 3 0 7c0 5 7 11 7 11s7-6 7-11c0-4-3-7-7-7z" fill="#c9914a"/><circle cx="7" cy="7" r="2.5" fill="#fff"/></svg></span>
    <span>465, Lorum Ipsum Dolore Sed,<br>United States</span>
  </div>
  <div class="f-contact" style="top:149px">
    <span class="f-icon"><svg width="16" height="16" viewBox="0 0 16 16"><path d="M3 1c2-1 3 0 4 3l0 1c0 1-1 2-2 3 1 2 2 3 4 4 1-1 2-2 3-2l1 0c3 1 3 2 3 4-1 2-3 2-6 1-4-2-6-4-8-8-1-3 0-5 1-6z" fill="#c9914a"/></svg></span>
    <span>+1 (555) 014 2290</span>
  </div>
  <div class="f-contact" style="top:199px">
    <span class="f-icon"><svg width="16" height="12" viewBox="0 0 16 12"><rect width="16" height="12" rx="1.5" fill="#c9914a"/><polyline points="1,1 8,7 15,1" fill="none" stroke="#fff" stroke-width="1.5"/></svg></span>
    <span>info@kestrada.com</span>
  </div>

  <div class="f-rule" style="top:266px"></div>
  <div class="f-brand"><span class="dot"></span>Kestrada</div>
  <div class="f-legal">LEGAL SUPPORT &nbsp;|&nbsp; COOKIES &nbsp;|&nbsp; PRIVACY POLICY</div>
  <div class="f-rule" style="top:344px"></div>
  <div class="f-copy">© 2025 Kestrada &nbsp;|&nbsp; All Rights Reserved</div>
  <div class="social gold" style="left:960px">Netly</div>
  <div class="social" style="left:1004px">Pixo</div>
  <div class="social" style="left:1049px">Prolink</div>
</footer>

</body>
</html>
```